Mobile Repair Service on location needs a Web Design

We are starting a new mobile device repair service called Handset Haven and our website needs a design!

Hello Designers!
First, we'd like to make clear this is more than a simple web design contest, we want the designers to create an idea. We want someone who can create the whole theme of the service's we provide. We want someone that can help design our visual branding, help us communicate a sentiment. And we are willing to pay for that.

Who are we?
Our company is based in Rotterdam, the Netherlands. We provide different services for all kinds of electronic devices. The kind of services we provide are, among other things, installations of hardware and software and the repair of broken or malfunctioning devices.
We are starting a new service that offers mobile device repairs on location, be it at the home of our customers, their office, or any other place. Just give us the address and we will come to you for the repair job. This is also our main USP. We have multiple skilled engineers who drive trough the country on a daily basis and can be on location within a working day. Repair is done immediately onsite while the customer waits. At this stage we will start with the smartphone product-group within the mobile devices. In a second phase we might also add tablets.
People don't want to be without their phone for weeks because of some parts that needed to be ordered by a repair center they had to sent their phone to. We offer a fully functional mobile repair center in the form of specially customized vans. These vans have all the tools and utilities needed by our engineers to safely repair your mobile device. Your phone is being repaired directly in front of you, the next business-day, on a location you desire.

For this new service we are creating a website called Handset Haven. The website needs a story and matching design and this is where you come in. We are not looking for a simple template design we can get from any place. We need a story. We want you to create an idea, build a unique theme or vision that helps sell the product/service. This goes beyond the design of the website. We need the whole package, the design you are creating needs to have returning elements like icons, color use, images, maybe even characters etc. You name it! There needs to be a common thread in the design so we can reuse elements in, for example, the email templates, the work order or receipt we give to our customers (we may contact the winner of the contest to design these for us as well!).

The name 'Handset Haven' is chosen. Rehab (short for rehabilitate) has a bold and playful tone to it and the design needs to reflect the name. So we're looking for a somewhat playful and cheeky design. Definitely not too serious and definitely modern. We already got a logo that we love and that fit's this description (see attached design documents for the logo). It's bold, powerful and fun. Our web design needs to reflect this as well and has to fit in with our logo.
We would really like it if the design somehow incorporates elements that highlight our unique selling points (repairs on location, we come to you etc.). We would really like some form of story telling in the design. Think clumsy people breaking their phones. Teenagers in tears because they have no access to their friends. People nowadays have the need to always be 'connected'. What happens when your phone is broken or malfunctioning? We're handling tech, we are nerds and a little bit weird, but we're professionals and here to help you with your problem. The sentiment Byte Brigade tries to communicate is something we really like. We're looking for fresh idea's, anything goes!

In an overview all Unique Selling Points of the Handset haven service:
- Professional service on location. Don’t ship to us we will come to you!
- Clear pricing upfront. No hidden cost.
- Next business-day repair.
- Backed by a professional call center open 12 hours a day and open on a Saturday as well
- Backed by a professional repair center with more then 12 years of experience
- Repair is done by certified engineers
- 1 year warranty on the repair

The process:
The main function of our website will be for customers to make a repair request. A customer will visit our website and can make a repair request immediately by going through a 'request-order-flow'. In this flow he or she will need to fill in some forms and can select wich type/model/brand of mobile device he or she has and what parts need to be repaired. After a request is placed we will call the customer back (within an hour) for a short intake and to set a date/time and location. Our engineer will meet the customer at the specified location and will repair the device onsite in one of our mobile repair centers, which is a specialized van equipped with all the tools needed for device restorations.
So in short the steps are:
- Choose your device and repair job
- Place the order
- Get a callback within the hour
- Set date and location
- We will come to you.

Website functionality:
Our website is our main form of communication. So the sentiment we want to communicate needs be reflected in the design. We need a main/front page designed (preferably a long scrolling page design) containing:
1. Customers will be able to request a repair job directly on our website. So there will need to be a prominent button/link at the top of our main page that will bring the customer to this 'request-order-flow'. This is the main flow which needs to be full focus on the front page. All other items are secondary.
2. The general information of who we are and what we do, and why the customer should choose us. Preferably in short bullet-point type keywords/sentences with icons or other visual cues. See our unique selling points to get an idea of the information that will be displayed here.
3. There needs to be a section that will explain the process (see above) of a repair request step-by- step, again in brief short key sentences and with (custom) icons.
4. There needs to be a section that explains to the customer he/she can always contact us if they are not sure what the problem is with their device, and for this reason are not sure what repair request they should order.
5. We want to implement some functionality that display customer ratings or customer reviews. So there needs to be room for some kind of widget of plugin we're going to implement which shows these reviews.
6. A 'For business section' where we will explain all the options we provide for corporate clients.
7. Social media links.
8. There needs to be a menu with buttons that leads to the all sections described in the previous points.

For now, we need a design for our front page. In the second phase, when we have picked our winner, we may ask the winner to design the page(s) for our request workflow as well.

EDIT:
Finally, we have a very specific order in mind for the different segments of our website. We would like you to add some more segments that were not in our original brief as well:

1. Top header with order/request button. (should instantly make clear our main USP, we do repairs on location)
2. Our process
3. Our unique selling points / why choose us
4. The kind of repairs we do (broken screens, broken batteries, water damage, broken camera's, no sound etc.)
5. A 'meet our team' section, where we introduce some of our engineers
6. A 'contact us for any questions' section/
7. Testimonials/user reviews
8. A section where we show key performance indicators
9. 'For businesses' sections
10.'Subscribe for newsletter' field
11. Social media buttons

Industry/Entity Type

It Service

Number of Pages Required

1 page

Font styles to use
Sans Serif

Requirements
Must have
• a main/front page, design only
• custom icons/images for banners, adverts online and in print (high res)
Nice to have
• Storytelling in our design.
• Design that fits with our brand new logo.
• Elements like icons to have a flat design.
• Keep in mind that the website will need to be responsive when designing! (Ideally provide an example of the mobile design as well)
• Create a fun and trustworthy feeling.

```html
<!DOCTYPE html>
<html lang="en">
<head>
<meta charset="utf-8">
<title>Handset Haven – Mobile Repair Service</title>
<link href="https://fonts.googleapis.com/css2?family=Raleway:wght@200;300;400;500;600;700;800&display=swap" rel="stylesheet">
<style>
:root{
  --orange:#ef5a24;
  --orange-dark:#d9461a;
  --ink:#1c1c1c;
  --grey:#666;
  --grey-light:#9a9a9a;
  --line:#e3e3e3;
  --lavender:#e6e5f2;
  --ring:#c9c8ea;
  --icon-bg:#4a4d57;
  --navy:#171c27;
  --white:#fff;
}
*{margin:0;padding:0;box-sizing:border-box}
html,body{width:1200px;height:3797px;overflow:hidden}
body{font-family:'Raleway',sans-serif;color:var(--ink);background:var(--white);position:relative}
section,header,footer{position:absolute;left:0;width:1200px}
.btn{display:inline-block;background:var(--orange);color:var(--white);font-size:14px;font-weight:500;border-radius:20px;padding:9px 26px;text-decoration:none}

/* header */
.site-header{top:0;height:106px;background:var(--white)}
.brand{position:absolute;left:84px;top:18px;display:flex;align-items:center;gap:10px}
.brand-mark{width:44px;height:44px;border-radius:50%;background:var(--orange)}
.brand-name{font-weight:800;font-size:22px;line-height:1.05;color:var(--ink);width:110px}
.brand-tag{position:absolute;left:54px;top:52px;font-size:10px;color:var(--orange);font-weight:600;white-space:nowrap}
.main-nav{position:absolute;left:398px;top:45px;display:flex;gap:14px;font-size:13px;white-space:nowrap}
.main-nav a{color:#333;text-decoration:none}
.main-nav a.active{color:var(--orange)}
.site-header .btn{position:absolute;left:987px;top:33px;width:132px;text-align:center;padding:10px 0}

/* hero */
.hero{top:106px;height:603px}
.hero-photo{position:absolute;inset:0;background:linear-gradient(120deg,#5a4a3c 0%,#3b3129 40%,#6d5a48 70%,#2e2722 100%);clip-path:polygon(0 0,100% 0,100% 78%,0 100%)}
.hero-photo::after{content:"";position:absolute;inset:0;background:rgba(20,15,12,.35)}
.hero-copy{position:absolute;top:180px;left:0;width:1200px;text-align:center;color:var(--white)}
.hero-title{font-weight:300;font-size:46px;line-height:1.1}
.hero-title span{display:block;color:#dfe5f7}
.hero-text{font-size:17px;font-weight:400;margin:12px auto 22px;width:900px;line-height:1.45}

/* intro */
.intro{top:709px;height:481px;display:flex;justify-content:center;padding-top:55px}
.intro-col{width:370px;text-align:center;padding:0 32px;border-right:1px solid var(--line);height:370px}
.intro-col:last-child{border-right:none}
.intro-icon{height:50px;display:flex;justify-content:center;align-items:center}
.intro-title{font-size:26px;font-weight:300;margin-top:18px;line-height:1.15}
.intro-title b{display:block;font-weight:700}
.intro-text{font-size:12.5px;line-height:1.8;color:var(--grey);margin:14px 0 20px}

/* services */
.services{top:1190px;height:562px;background:linear-gradient(110deg,#f37a3a 0%,#ef5a24 45%,#f4894a 75%,#e9541f 100%);color:var(--white)}
.section-head{text-align:center;font-size:30px;font-weight:300;line-height:1.2}
.section-head b{display:block;font-weight:700}
.section-head::after{content:"";display:block;width:40px;height:3px;background:var(--orange);margin:10px auto 0}
.services .section-head{padding-top:50px}
.services .section-head::after{background:var(--white)}
.service-list{position:absolute;top:196px;left:0;width:1200px;height:340px}
.service{position:absolute;width:150px;margin-left:-75px;text-align:center}
.service-ring{width:126px;height:126px;border-radius:50%;background:var(--ring);margin:0 auto;display:flex;align-items:center;justify-content:center}
.service-core{width:92px;height:92px;border-radius:50%;background:var(--icon-bg);display:flex;align-items:center;justify-content:center}
.service-stem{width:2px;height:40px;background:rgba(255,255,255,.5);margin:0 auto}
.service-dot{width:12px;height:12px;border-radius:50%;background:#3a3a3a;border:2px solid rgba(255,255,255,.6);margin:0 auto 18px}
.service p{font-size:12px;line-height:1.55}
.service strong{font-weight:700;font-size:13px}

/* process */
.process{top:1752px;height:572px}
.process .section-head{padding-top:60px;color:var(--ink)}
.steps{position:absolute;top:173px;left:0;width:1200px}
.step{position:absolute;width:200px;margin-left:-100px;text-align:center}
.step-art{width:130px;height:210px;margin:0 auto;border-radius:10px;background:linear-gradient(180deg,#f4f4f6,#e6e7ec)}
.step h3{font-size:14px;font-weight:500;color:var(--orange);line-height:1.5;margin-top:28px}
.step p{font-size:11.5px;color:var(--grey);line-height:1.6;margin-top:8px}

/* help */
.help{top:2324px;height:461px;background:linear-gradient(90deg,#f5f1ec 0%,#fbf9f7 55%,#f3efe9 100%)}
.help-photo{position:absolute;right:0;top:0;width:466px;height:461px;background:linear-gradient(135deg,#e8e2da 0%,#c9b6a3 50%,#f1ece5 100%)}
.help-copy{position:absolute;left:80px;top:75px;width:640px}
.help-lead{font-size:29px;color:var(--orange);font-weight:400;line-height:1.45}
.help-strong{font-size:29px;font-weight:700;line-height:1.45;margin:16px 0 22px}

/* testimonials */
.testimonials{top:2785px;height:400px}
.testimonials .section-head{padding-top:58px}
.quote{position:absolute;top:203px;display:flex;align-items:flex-start}
.quote-avatar{width:128px;height:128px;border-radius:50%;border:5px solid var(--orange);background:linear-gradient(160deg,#d8d2cc,#a9a19a);flex:none;position:relative}
.quote-avatar::after{content:"";position:absolute;right:-16px;top:40px;border:10px solid transparent;border-left:14px solid var(--orange)}
.quote-body{margin-left:38px;width:300px;font-size:12.5px;color:var(--grey);line-height:1.7;position:relative;padding:8px 22px 0}
.quote-body::before,.quote-body::after{font-size:40px;font-weight:700;color:var(--ink);position:absolute;line-height:1}
.quote-body::before{content:"\201C";left:0;top:2px}
.quote-body::after{content:"\201D";right:0;top:32px}
.quote-author{display:block;color:var(--orange);margin-top:16px}

/* business */
.business{top:3185px;height:215px;background:var(--lavender)}
.business-label{position:absolute;left:78px;top:85px;width:150px;text-align:center;font-size:29px;font-weight:300;line-height:1.15}
.business-label b{display:block;font-weight:700}
.business-divider{position:absolute;left:253px;top:70px;width:1px;height:100px;background:#b9b8cc}
.business-body{position:absolute;left:311px;top:50px}
.business-body h2{font-size:31px;font-weight:400}
.business-body ul{list-style:none;margin-top:14px}
.business-body li{font-size:14px;font-weight:700;color:var(--orange);line-height:1.85}
.business-body li::before{content:"•";margin-right:6px}

/* footer */
.site-footer{top:3400px;height:347px;background:linear-gradient(120deg,#1b2130,#131722 60%,#1e2433);color:#d6d6d6}
.footer-col{position:absolute;top:72px}
.footer-col h4{color:var(--orange);font-size:16px;font-weight:500;padding-bottom:8px;border-bottom:1px solid #3b4150;width:250px;margin-bottom:14px}
.footer-col ul{list-style:none;font-size:12.5px;line-height:1.72}
.footer-col li::before{content:"•";margin-right:7px}
.contact-line{display:flex;gap:10px;font-size:12.5px;line-height:1.5;margin-bottom:8px;align-items:flex-start}
.contact-line .accent{color:var(--orange)}
.newsletter p{font-size:12.5px;line-height:1.5;width:240px}
.newsletter .field{width:200px;height:26px;background:var(--white);margin:12px 0 10px;font-size:10px;color:#999;padding:6px 8px}
.newsletter .btn{font-size:11px;padding:5px 12px;border-radius:3px}
.social li{list-style:none;display:flex;align-items:center;gap:10px;font-size:12.5px;margin-bottom:12px}
.social li::before{content:none}
.social .sq{width:20px;height:20px;background:#5e6fa8;border-radius:3px}
.copyright{top:3747px;height:50px;background:var(--orange);color:var(--white);font-size:11px;text-align:center;line-height:50px}
</style>
</head>
<body>

<header class="site-header">
  <div class="brand">
    <span class="brand-mark"></span>
    <span class="brand-name">HANDSET HAVEN</span>
    <span class="brand-tag">We will come to you!</span>
  </div>
  <nav class="main-nav">
    <a class="active" href="#home">Home</a>
    <a href="#who">Who We Are</a>
    <a href="#what">What We Do</a>
    <a href="#process">Our Process</a>
    <a href="#pricing">Pricing</a>
    <a href="#testimonials">Testimonials</a>
    <a href="#clients">Our Clients</a>
  </nav>
  <a class="btn" href="#contact">Contact Us</a>
</header>

<section class="hero" id="home">
  <div class="hero-photo" role="img" aria-label="Technician repairing a phone at a workbench"></div>
  <div class="hero-copy">
    <h1 class="hero-title">Best Mobile Repair Service <span>At Any Time In Anywhere</span></h1>
    <p class="hero-text">We are starting a new service that offers mobile device repairs on location, be it at the home of our customers, their office, or any other place. Just give us the address and we will come to you for the repair job.</p>
    <a class="btn" href="#call">Call Now</a>
  </div>
</section>

<section class="intro">
  <div class="intro-col" id="who">
    <div class="intro-icon"><svg width="50" height="44" viewBox="0 0 50 44"><g fill="#ef5a24"><circle cx="25" cy="10" r="7"/><circle cx="11" cy="16" r="5"/><circle cx="39" cy="16" r="5"/><path d="M14 40c0-9 5-15 11-15s11 6 11 15z"/><path d="M2 40c0-7 4-12 9-12 2 0 3 1 4 2-2 3-3 6-3 10z"/><path d="M48 40c0-7-4-12-9-12-2 0-3 1-4 2 2 3 3 6 3 10z"/></g></svg></div>
    <h2 class="intro-title">Who <b>We Are</b></h2>
    <p class="intro-text">Our company is based in Rotterdam, the Netherlands. We provide different services for all kinds of electronic devices. The kind of services we provide are, among other things, installations of hardware and software and the repair of broken or malfunctioning devices.</p>
    <a class="btn" href="#more">Read More</a>
  </div>
  <div class="intro-col" id="what">
    <div class="intro-icon"><svg width="28" height="48" viewBox="0 0 28 48"><rect x="2" y="2" width="24" height="44" rx="4" fill="none" stroke="#ef5a24" stroke-width="3"/><rect x="7" y="9" width="14" height="26" fill="#333"/><circle cx="14" cy="40" r="2" fill="#ef5a24"/></svg></div>
    <h2 class="intro-title">What <b>We Do</b></h2>
    <p class="intro-text">We are starting a new service that offers mobile device repairs on location, be it at the home of our customers, their office, or any other place. Just give us the address and we will come to you for the repair job. We offer a fully functional mobile repair center in the form of specially customized vans.</p>
    <a class="btn" href="#more">Read More</a>
  </div>
  <div class="intro-col">
    <div class="intro-icon"><svg width="34" height="48" viewBox="0 0 34 48"><circle cx="12" cy="8" r="6" fill="#ef5a24"/><path d="M9 18h6v12l10 2c4 1 5 4 4 8l-2 8H11L4 34l3-3 2 2z" fill="#222"/></svg></div>
    <h2 class="intro-title">Why <b>Choose Us</b></h2>
    <p class="intro-text">We have multiple skilled engineers who drive trough the country on a daily basis and can be on location within a working day. Repair is done immediately onsite while the customer waits. Your phone is being repaired directly in front of you, the next business-day, on a location you desire.</p>
    <a class="btn" href="#more">Read More</a>
  </div>
</section>

<section class="services" role="img" aria-label="Hand holding a smartphone, tinted orange">
  <h2 class="section-head">Our <b>Services</b></h2>
  <div class="service-list">
    <div class="service" style="left:144px">
      <div class="service-ring"><div class="service-core"><svg width="40" height="40" viewBox="0 0 40 40"><path d="M20 4a11 11 0 0 0-11 11c0 8 11 21 11 21s11-13 11-21A11 11 0 0 0 20 4z" fill="#fff"/><circle cx="20" cy="15" r="4" fill="#4a4d57"/></svg></div></div>
      <div class="service-stem"></div><div class="service-dot"></div>
      <p><strong>Professional service</strong> on location. Don't ship to us we will come to you!</p>
    </div>
    <div class="service" style="left:291px">
      <div class="service-ring"><div class="service-core"><svg width="40" height="40" viewBox="0 0 40 40"><path d="M4 20 20 4h14v14L18 34z" fill="#fff"/><circle cx="27" cy="11" r="3" fill="#4a4d57"/></svg></div></div>
      <div class="service-stem"></div><div class="service-dot"></div>
      <p><strong>Clear pricing upfront.</strong><br>No hidden cost.</p>
    </div>
    <div class="service" style="left:446px">
      <div class="service-ring"><div class="service-core"><svg width="40" height="40" viewBox="0 0 40 40"><path d="M10 5c2-1 4 0 5 2l3 6c1 2 0 3-1 4l-2 2c2 4 5 7 9 9l2-2c1-1 2-2 4-1l6 3c2 1 3 3 2 5-2 5-6 6-10 4C17 33 8 24 6 15c-1-4 0-8 4-10z" fill="#fff"/></svg></div></div>
      <div class="service-stem"></div><div class="service-dot"></div>
      <p><strong>Backed by a professional call center</strong> open 12 hours a day and open on a Saturday as well</p>
    </div>
    <div class="service" style="left:600px">
      <div class="service-ring"><div class="service-core"><svg width="40" height="40" viewBox="0 0 40 40"><rect x="5" y="8" width="30" height="27" rx="3" fill="none" stroke="#fff" stroke-width="3"/><rect x="5" y="8" width="30" height="7" fill="#fff"/><g fill="#fff"><rect x="10" y="19" width="5" height="4"/><rect x="18" y="19" width="5" height="4"/><rect x="26" y="19" width="5" height="4"/><rect x="10" y="26" width="5" height="4"/><rect x="18" y="26" width="5" height="4"/></g></svg></div></div>
      <div class="service-stem"></div><div class="service-dot"></div>
      <p><strong>Next business-day</strong><br>repair.</p>
    </div>
    <div class="service" style="left:755px">
      <div class="service-ring"><div class="service-core"><svg width="40" height="40" viewBox="0 0 40 40"><g stroke="#fff" stroke-width="5" stroke-linecap="round"><path d="M8 8l24 24"/><path d="M32 8 8 32"/></g></svg></div></div>
      <div class="service-stem"></div><div class="service-dot"></div>
      <p><strong>Backed by a professional repair center</strong> with more then 12 years of experience come to you!</p>
    </div>
    <div class="service" style="left:906px">
      <div class="service-ring"><div class="service-core"><svg width="40" height="40" viewBox="0 0 40 40"><g fill="#fff"><circle cx="13" cy="13" r="5"/><circle cx="27" cy="13" r="5"/><path d="M4 33c0-7 4-12 9-12s9 5 9 12z"/><path d="M18 33c0-7 4-12 9-12s9 5 9 12z"/></g></svg></div></div>
      <div class="service-stem"></div><div class="service-dot"></div>
      <p><strong>Repair is done by</strong> certified engineers.</p>
    </div>
    <div class="service" style="left:1058px">
      <div class="service-ring"><div class="service-core"><svg width="40" height="40" viewBox="0 0 40 40"><circle cx="20" cy="15" r="11" fill="#fff"/><circle cx="20" cy="15" r="5" fill="#4a4d57"/><path d="M13 24l-4 12 6-3 3 5 2-10zM27 24l4 12-6-3-3 5-2-10z" fill="#fff"/></svg></div></div>
      <div class="service-stem"></div><div class="service-dot"></div>
      <p><strong>1 year warranty</strong><br>on the repair.</p>
    </div>
  </div>
</section>

<section class="process" id="process">
  <h2 class="section-head">Our <b>Process</b></h2>
  <div class="steps">
    <div class="step" style="left:170px">
      <div class="step-art" role="img" aria-label="Cartoon engineer choosing a device"></div>
      <h3>Choose your device<br>and repair job</h3>
      <p>Suspendisse iaculis elit nec ornare pellentes. Donec lacinia lectus malesuada.</p>
    </div>
    <div class="step" style="left:382px">
      <div class="step-art" role="img" aria-label="Cartoon engineer placing an order"></div>
      <h3>Place the<br>order</h3>
      <p>Suspendisse iaculis elit nec ornare pellentes. Donec lacinia lectus malesuada.</p>
    </div>
    <div class="step" style="left:600px">
      <div class="step-art" role="img" aria-label="Cartoon engineer waiting for a callback"></div>
      <h3>Get a callback within<br>the hour</h3>
      <p>Suspendisse iaculis elit nec ornare pellentes. Donec lacinia lectus malesuada.</p>
    </div>
    <div class="step" style="left:815px">
      <div class="step-art" role="img" aria-label="Cartoon engineer holding a date and location sign"></div>
      <h3>Set date and<br>location</h3>
      <p>Suspendisse iaculis elit nec ornare pellentes. Donec lacinia lectus malesuada.</p>
    </div>
    <div class="step" style="left:1028px">
      <div class="step-art" role="img" aria-label="Cartoon engineer arriving with a tablet"></div>
      <h3>We will come<br>to you</h3>
      <p>Suspendisse iaculis elit nec ornare pellentes. Donec lacinia lectus malesuada.</p>
    </div>
  </div>
</section>

<section class="help" id="contact">
  <div class="help-photo" role="img" aria-label="Smiling customer talking on a phone"></div>
  <div class="help-copy">
    <p class="help-lead">You are not sure what the problem is with their device, and for this reason you are not sure what repair request they should order.</p>
    <p class="help-strong">Dont Worry, You can always contact us whatever the problem you have.</p>
    <a class="btn" href="#contact">Contact Us</a>
  </div>
</section>

<section class="testimonials" id="testimonials">
  <h2 class="section-head">Clients' <b>Testimonials</b></h2>
  <div class="quote" style="left:84px">
    <div class="quote-avatar" role="img" aria-label="Customer portrait"></div>
    <p class="quote-body">Donec turpis turpis, dapibus sed turpis vel, condimentum ultricies sem leo magna condimentum nulla.<span class="quote-author">- Mira Solen</span></p>
  </div>
  <div class="quote" style="left:620px">
    <div class="quote-avatar" role="img" aria-label="Customer portrait"></div>
    <p class="quote-body">Donec turpis turpis, dapibus sed turpis vel, condimentum ultricies sem leo magna condimentum nulla.<span class="quote-author">- Tom Ardel</span></p>
  </div>
</section>

<section class="business" id="clients">
  <h2 class="business-label">For <b>Businees</b></h2>
  <div class="business-divider"></div>
  <div class="business-body">
    <h2>The services we provide for corporate clients are-</h2>
    <ul>
      <li>In nec orci at diam sollicitudin mollis.</li>
      <li>Nunc venenatis ligula id purus varius, quis dapibus erat auctor.</li>
      <li>Suspendisse in diam vitae ex commodo commodo.</li>
    </ul>
  </div>
</section>

<footer class="site-footer">
  <div class="footer-col" style="left:78px">
    <h4>Quick Links</h4>
    <ul>
      <li>Home</li><li>Who We Are</li><li>What We Do</li><li>Our Process</li><li>Pricing</li><li>Testimonials</li><li>Our Clients</li><li>Contact Us</li>
    </ul>
  </div>
  <div class="footer-col" style="left:304px">
    <h4>Contact Information</h4>
    <div class="contact-line"><svg width="12" height="16" viewBox="0 0 12 16"><path d="M6 0a6 6 0 0 0-6 6c0 4 6 10 6 10s6-6 6-10a6 6 0 0 0-6-6z" fill="#fff"/></svg><span>Lorem ipsum dolor sit amet<br>0417 552 9083<br>PO Box 4827 Harbor DC 3190</span></div>
    <div class="contact-line"><svg width="12" height="14" viewBox="0 0 12 14"><path d="M3 0l3 4-2 2c1 2 2 3 4 4l2-2 2 3-2 3C5 13 0 8 0 3z" fill="#fff"/></svg><span class="accent">Freecall 0800 314 2760</span></div>
    <div class="contact-line"><svg width="14" height="10" viewBox="0 0 14 10"><rect width="14" height="10" fill="#fff"/><path d="M0 0l7 6 7-6" stroke="#171c27" fill="none"/></svg><span>info@handsethaven.com</span></div>
  </div>
  <div class="footer-col newsletter" style="left:640px">
    <h4>Newsletter Signup</h4>
    <p>Please enter your email address below to receive our FREE newsletter</p>
    <div class="field">Your Email ID</div>
    <a class="btn" href="#subscribe">Subscribe</a>
  </div>
  <div class="footer-col social" style="left:932px">
    <h4>Follow Us</h4>
    <ul>
      <li><span class="sq"></span>Gatherly</li>
      <li><span class="sq"></span>Workwave</li>
      <li><span class="sq"></span>Quipster</li>
      <li><span class="sq"></span>Email</li>
    </ul>
  </div>
</footer>

<footer class="copyright">Copyright 2015@handsethaven.com . All Rights Are Reserved</footer>

</body>
</html>
```